2 Labels Pet Treat Label Hemp Extract "Dogs and Cats"

We are currently looking for an "easy on the eye" type of pet treat label. Our colors are mostly Black and Gold however, we are open to suggestions. First label is your normal "Hemp Extract Pet Treat". Second label is "Hemp Extract for Pain & Inflammation plus calming" We would like to work with you on inputting the small details. Please use buzzwords such as Veterinary recommended etc. We would like our Logo on there as well if possible. Please make room for Ingredient list as well. A search on google for Pet treats CBD... or in this case "Hemp Extract" that should give you some idea of what we are looking for. I normally use Canva however, if you can show us how to make edits for future use, we would appreciate that.. FYI. It's 30 dog treats in a bag. 5mg of Hemp Extract. Totaling 150mg of Hemp Extract.
The 2 Logos should only be different in color since one is for Pain and Inflamation plus calming. and the other is just hemp extract.

Target Market(s)

Dogs & Cats

Font styles to use
Decorative
Script
Other font styles liked:
• Bebas Nuee

Requirements
Must have
• Must Say Hemp Extract and not CBD. Must have 5mg of Hemp Extract. Must have a few buzz words such as Veterinarian recommended, Must say Grain Free. No Dairy.
• The label needs to be on a 3" x 4.5" Sticker. So essentially the label is just a sticker vs the whole bag.
• The sticker will go a brown kraft bag, but the label for this project will be on a 3" x 4.5" Sticker.
Should not have
• CBD

```html
<!DOCTYPE html>
<html lang="en">
<head>
<meta charset="utf-8">
<title>Sereno Hemp – Hemp Extract Pet Treat Label</title>
<link rel="stylesheet" href="https://fonts.googleapis.com/css2?family=Bebas+Neue&family=Montserrat:wght@300;400;500;600;700;800;900&display=swap">
<style>
  :root {
    --ink: #0d0d0d;
    --charcoal: #1c1c1c;
    --charcoal-light: #2e2e2e;
    --gold: #c9a66b;
    --gold-deep: #a88547;
    --gold-light: #e3c892;
    --white: #ffffff;
    --badge-red: #c8363a;
    --badge-blue: #2c3f7a;
  }
  * { margin: 0; padding: 0; box-sizing: border-box; }
  html, body { width: 1200px; height: 800px; overflow: hidden; background: var(--ink); }
  .label {
    position: relative;
    width: 1200px;
    height: 800px;
    overflow: hidden;
    font-family: "Montserrat", sans-serif;
    color: var(--white);
    background:
      radial-gradient(ellipse at 35% 45%, var(--charcoal-light) 0%, var(--charcoal) 45%, var(--ink) 100%);
  }

  /* Brand name */
  .brand {
    position: absolute;
    left: 92px;
    top: 150px;
    width: 240px;
    display: flex;
    align-items: center;
    justify-content: center;
    gap: 12px;
  }
  .brand-dot {
    width: 18px; height: 18px;
    border-radius: 50%;
    background: var(--gold);
  }
  .brand-name {
    font-weight: 600;
    font-size: 22px;
    letter-spacing: 0.28em;
    white-space: nowrap;
    color: var(--gold);
  }

  /* Headline */
  .headline-hemp {
    position: absolute;
    left: 78px;
    top: 208px;
    font-weight: 900;
    font-size: 156px;
    line-height: 1;
    letter-spacing: -2px;
    color: var(--white);
  }
  .headline-extract {
    position: absolute;
    left: 80px;
    top: 358px;
    font-weight: 400;
    font-size: 106px;
    line-height: 1;
    letter-spacing: -1px;
    color: var(--gold);
  }
  .headline-rule {
    position: absolute;
    left: 84px;
    top: 478px;
    width: 334px;
    height: 1px;
    background: var(--gold);
  }

  /* Benefit line */
  .benefit {
    position: absolute;
    left: 83px;
    top: 500px;
    font-size: 35px;
    line-height: 41px;
    font-weight: 400;
    color: var(--white);
  }
  .benefit strong { font-weight: 800; color: var(--gold); }

  .description {
    position: absolute;
    left: 83px;
    top: 600px;
    width: 540px;
    font-size: 17px;
    line-height: 22px;
    font-weight: 500;
    color: var(--white);
  }
  .description .diet-claims { font-weight: 700; color: var(--gold); }

  /* Trust marks */
  .mark-packed {
    position: absolute;
    left: 76px;
    top: 690px;
    width: 84px;
    height: 84px;
  }
  .mark-thc {
    position: absolute;
    left: 202px;
    top: 692px;
    width: 128px;
    text-align: center;
  }
  .mark-thc .percent {
    font-weight: 900;
    font-size: 42px;
    line-height: 42px;
    color: var(--white);
  }
  .mark-thc .tag {
    margin-top: 3px;
    background: var(--gold);
    color: var(--white);
    font-weight: 700;
    font-size: 21px;
    line-height: 26px;
  }
  .mark-natural {
    position: absolute;
    left: 372px;
    top: 694px;
    width: 140px;
    height: 76px;
  }
  .mark-natural span {
    position: absolute;
    left: 0; right: 0;
    top: 34px;
    text-align: center;
    font-weight: 600;
    font-size: 17px;
    color: var(--white);
  }

  /* Gold band */
  .gold-band {
    position: absolute;
    left: 730px;
    top: 0;
    width: 370px;
    height: 800px;
    background: linear-gradient(180deg, var(--gold-light) 0%, var(--gold) 55%, var(--gold-deep) 100%);
  }
  .claim-organic {
    position: absolute;
    left: 730px;
    width: 370px;
    top: 50px;
    text-align: center;
    font-family: "Bebas Neue", sans-serif;
    color: var(--white);
  }
  .claim-organic .big { font-size: 66px; line-height: 60px; letter-spacing: 1px; }
  .claim-organic .small {
    font-size: 46px; line-height: 46px;
    letter-spacing: 0.22em;
    color: var(--ink);
    margin-top: 2px;
  }
  .claim-vet {
    position: absolute;
    left: 730px;
    width: 370px;
    top: 176px;
    text-align: center;
    color: var(--white);
  }
  .claim-vet .big { font-weight: 900; font-size: 45px; line-height: 50px; letter-spacing: -0.5px; }
  .claim-vet .small { font-weight: 500; font-size: 33px; line-height: 36px; letter-spacing: 1px; }

  .pet-photo {
    position: absolute;
    left: 762px;
    top: 268px;
    width: 378px;
    height: 526px;
    border-radius: 140px 140px 20px 20px;
    background: linear-gradient(160deg, #f1ece4 0%, #d9cbb4 45%, #8a6a45 75%, #3a2c20 100%);
  }

  .count-badge {
    position: absolute;
    left: 631px;
    top: 568px;
    width: 200px;
    height: 200px;
  }
</style>
</head>
<body>
<main class="label">

  <div class="brand">
    <span class="brand-dot"></span>
    <span class="brand-name">SERENO HEMP</span>
  </div>

  <h1 class="headline-hemp">HEMP</h1>
  <h2 class="headline-extract">EXTRACT</h2>
  <div class="headline-rule"></div>

  <p class="benefit">FOR PAIN &amp; <strong>INFLAMMATION</strong><br><strong>PLUS CALMING</strong></p>

  <p class="description">Specially formulated to assist canines with pain, inflammation, stress, anxiety, age-related issues and overall health &amp; wellness. <span class="diet-claims">Grain Free. No Dairy.</span></p>

  <svg class="mark-packed" viewBox="0 0 84 84" aria-label="Packed in the USA">
    <defs>
      <path id="packed-arc" d="M12 70 A36 36 0 1 0 74 22"/>
    </defs>
    <circle cx="32" cy="37" r="27" fill="var(--white)"/>
    <circle cx="32" cy="37" r="24" fill="var(--badge-red)"/>
    <rect x="8" y="13" width="22" height="22" fill="var(--badge-blue)"/>
    <text font-family="Montserrat, sans-serif" font-size="9" font-weight="700" fill="var(--white)" letter-spacing="1">
      <textPath href="#packed-arc" startOffset="3%">PACKED IN THE USA</textPath>
    </text>
  </svg>

  <div class="mark-thc">
    <div class="percent">100%</div>
    <div class="tag">THC FREE</div>
  </div>

  <div class="mark-natural">
    <svg width="140" height="76" viewBox="0 0 140 76" aria-hidden="true">
      <path d="M38 24 A34 34 0 0 1 60 6" fill="none" stroke="var(--gold)" stroke-width="3"/>
      <path d="M80 6 A34 34 0 0 1 102 24" fill="none" stroke="var(--gold)" stroke-width="3"/>
      <path d="M44 62 A34 34 0 0 0 96 62" fill="none" stroke="var(--gold)" stroke-width="3"/>
    </svg>
    <span>ALL NATURAL</span>
  </div>

  <div class="gold-band"></div>

  <div class="claim-organic">
    <div class="big">ORGANICALLY</div>
    <div class="small">GROWN HEMP</div>
  </div>

  <div class="claim-vet">
    <div class="big">VETERINARY</div>
    <div class="small">RECOMMENDED</div>
  </div>

  <div class="pet-photo" role="img" aria-label="Photo of a sitting tri-colour collie dog beside a spotted tabby cat"></div>

  <svg class="count-badge" viewBox="0 0 200 200" aria-label="30 dog treats, 5mg each, totaling 150mg of hemp extract">
    <defs>
      <path id="badge-top" d="M34 100 A66 66 0 0 1 166 100"/>
      <path id="badge-bottom" d="M18 100 A82 82 0 0 0 182 100"/>
    </defs>
    <circle cx="100" cy="100" r="98" fill="var(--white)"/>
    <circle cx="100" cy="100" r="93" fill="var(--ink)"/>
    <circle cx="100" cy="100" r="54" fill="var(--white)"/>
    <circle cx="100" cy="100" r="50" fill="var(--gold)"/>
    <text font-family="Montserrat, sans-serif" font-size="14" font-weight="600" fill="var(--white)" letter-spacing="1.5">
      <textPath href="#badge-top" startOffset="50%" text-anchor="middle">30 DOG TREATS</textPath>
    </text>
    <text font-family="Montserrat, sans-serif" font-size="11" font-weight="600" fill="var(--white)" letter-spacing="0.4">
      <textPath href="#badge-bottom" startOffset="50%" text-anchor="middle">TOTALING 150MG OF HEMP EXTRACT</textPath>
    </text>
    <text x="100" y="112" text-anchor="middle" font-family="Montserrat, sans-serif" font-size="32" font-weight="800" fill="var(--white)">5mg</text>
  </svg>

</main>
</body>
</html>
```